Senior sex novelty store providing a private method for acquiring the products and knowledge

Our business supplies novelty sex products and services, specializing in the 50+ demographic. Products include sex products for individuals and couples. Services include webinars and teleseminars that address various sex and relationship issues. We are dedicated to providing discreet delivery of products and knowledge to people over 50 entering a new phase of life, facing new challenges. Our entire process from site through shipping is kept private to allow our customers the freedom to shop and learn in the privacy of their own home.

Target Market(s)

Seniors over 50 years old

Industry/Entity Type

Store

Number of Pages Required

1 page

Font styles to use
Serif

Requirements
Must have
• place for business description with a private look
Should not have
• anything sleazy

```html
<!DOCTYPE html>
<html lang="en">
<head>
<meta charset="utf-8">
<title>Evergreen Intimates – Private Store</title>
<link rel="stylesheet" href="https://fonts.googleapis.com/css2?family=Cinzel:wght@400;700&family=PT+Sans:wght@400;700&display=swap">
<style>
  :root{
    --gold:#b99c4e;
    --gold-light:#d2b668;
    --dark:#1f1a18;
    --ink:#2a2a2a;
    --white:#ffffff;
    --card-line:#d9d9d9;
    --footer:#161616;
    --serif:'Cinzel', Georgia, serif;
    --sans:'PT Sans', Arial, sans-serif;
  }
  *{box-sizing:border-box;margin:0;padding:0}
  html,body{width:1200px;height:3431px;overflow:hidden}
  body{font-family:var(--sans);background:var(--dark);color:var(--white)}
  .page{position:relative;width:1200px;height:3431px}

  /* Header */
  .site-header{position:relative;height:272px;background:linear-gradient(180deg,#2a2321,#1f1a19)}
  .brand{position:absolute;left:92px;top:52px;display:flex;align-items:center;gap:18px}
  .brand-mark{width:46px;height:46px;background:var(--gold)}
  .brand-name{font-family:var(--sans);font-size:40px;font-weight:400;color:var(--white);letter-spacing:1px;line-height:1}
  .brand-tag{font-size:21px;color:var(--white);letter-spacing:2px;margin-top:6px}
  .account{position:absolute;right:86px;top:72px;display:flex;gap:22px;font-size:13px;color:#ddd;letter-spacing:.5px}
  .account .cart{display:flex;align-items:center;gap:6px}
  .main-nav{position:absolute;left:0;right:0;top:214px;display:flex;justify-content:center;align-items:center;gap:30px;font-size:17px;text-transform:uppercase;letter-spacing:.5px}
  .main-nav a{color:var(--white);text-decoration:none}
  .main-nav a.active{color:var(--gold-light)}
  .main-nav .dot{width:5px;height:5px;border-radius:50%;background:#bbb}

  .hero{height:521px;background:
    radial-gradient(ellipse 18% 30% at 86% 28%, rgba(214,176,112,.85), rgba(214,176,112,0)),
    radial-gradient(ellipse 22% 42% at 66% 42%, rgba(226,178,152,.95), rgba(226,178,152,0)),
    radial-gradient(ellipse 24% 48% at 36% 40%, rgba(196,138,100,.95), rgba(196,138,100,0)),
    radial-gradient(ellipse 30% 40% at 30% 95%, rgba(150,100,74,.8), rgba(150,100,74,0)),
    linear-gradient(100deg,#1a1522 0%,#3a2a2c 40%,#5a3f38 65%,#2a1e22 100%)}

  /* Search */
  .search-bar{height:80px;background:var(--gold);display:flex;align-items:center;padding-left:106px}
  .search-label{font-size:20px;color:var(--white);text-transform:uppercase;width:218px}
  .search-field{height:35px;background:var(--white);border:1px solid #ccc;display:flex;align-items:center;padding-left:10px;gap:8px;font-size:12px;color:#777}
  .search-field svg{flex:none}
  .search-btn{height:35px;width:97px;background:#3b3b3b;color:#eee;font-size:13px;display:flex;align-items:center;justify-content:center;margin-left:14px}

  /* Store */
  .store{position:relative;height:1384px;background:
    radial-gradient(circle 60px at 8% 18%, rgba(220,170,110,.18), rgba(0,0,0,0)),
    radial-gradient(circle 80px at 94% 52%, rgba(220,170,110,.15), rgba(0,0,0,0)),
    radial-gradient(circle 70px at 12% 70%, rgba(230,190,140,.14), rgba(0,0,0,0)),
    radial-gradient(ellipse at 30% 35%,#4a3a36 0%,#2a2221 45%,#1d1818 100%)}
  .section-title{font-family:var(--serif);font-size:29px;text-align:center;letter-spacing:1px}
  .store .section-title{padding-top:102px}
  .rule{width:56px;height:2px;background:var(--gold);margin:14px auto 0}
  .store-intro{width:760px;margin:14px auto 0;text-align:center;font-size:17px;line-height:24px;color:#eee}
  .product-grid{position:absolute;left:93px;top:267px;display:grid;grid-template-columns:repeat(3,335px);column-gap:14px;row-gap:46px}
  .product-card{height:432px;background:var(--white);border:1px solid var(--card-line);color:var(--ink);text-align:center}
  .product-img{height:215px}
  .product-card h3{font-family:var(--serif);font-size:19px;font-weight:400;margin-top:20px;letter-spacing:.5px}
  .product-card .rule{width:36px;margin-top:10px}
  .product-card p{width:250px;margin:12px auto 0;font-size:12.5px;line-height:16px;color:#555}
  .card-actions{display:flex;justify-content:center;gap:10px;margin-top:20px}
  .btn-more{width:100px;height:38px;background:#e8e8e8;font-size:11px;color:#666;display:flex;align-items:center;justify-content:center;letter-spacing:.5px}
  .btn-cart{width:56px;height:38px;background:var(--gold);display:flex;align-items:center;justify-content:center}
  .see-more{position:absolute;left:0;right:0;top:1262px;text-align:center;font-family:var(--serif);font-size:22px;color:var(--gold)}

  /* News */
  .news{height:570px;background:var(--white);color:var(--ink);display:flex;gap:100px;padding:110px 92px 0}
  .news-col{width:545px}
  .news-col h2{font-family:var(--serif);font-size:31px;font-weight:400;color:var(--gold);line-height:40px}
  .news-col h3{font-size:17px;font-weight:400;line-height:23px;margin-top:40px;text-transform:uppercase;color:#222}
  .news-date{font-size:14px;color:var(--gold);margin-top:10px}
  .news-col p{font-size:14px;line-height:19px;color:#444;margin-top:16px}
  .read-more{font-size:14px;color:var(--gold);margin-top:40px;text-transform:uppercase}

  /* Subscribe */
  .subscribe{position:relative;height:518px}
  .subscribe-bg{position:absolute;inset:0;background:
    radial-gradient(ellipse 25% 40% at 72% 55%, rgba(120,100,110,.45), rgba(0,0,0,0)),
    radial-gradient(ellipse at 70% 40%,#4c3f44 0%,#2b2530 45%,#17141a 100%)}
  .subscribe-inner{position:relative;text-align:center}
  .social{position:absolute;top:-20px;left:0;right:0;display:flex;justify-content:center;gap:9px}
  .social span{width:40px;height:40px;border-radius:50%;background:var(--gold)}
  .subscribe h2{padding-top:80px;font-size:22px;font-weight:700;letter-spacing:1px}
  .subscribe p{font-size:17px;margin-top:14px;color:#e6e6e6}
  .subscribe-form{display:flex;justify-content:center;margin-top:38px}
  .subscribe-form .field{width:680px;height:44px;background:var(--white)}
  .subscribe-form .go{width:85px;height:44px;background:var(--gold);font-size:13px;display:flex;align-items:center;justify-content:center}
  .stats{display:flex;justify-content:center;margin-top:100px}
  .stat{width:225px;padding:0 28px;text-align:right;border-left:1px solid rgba(255,255,255,.35)}
  .stat:first-child{border-left:none}
  .stat strong{display:block;font-family:var(--serif);font-weight:400;font-size:26px;color:var(--gold)}
  .stat span{display:block;font-size:14px;color:#eee;margin-top:4px}

  /* Footer */
  .site-footer{height:86px;background:var(--footer);display:flex;align-items:center;justify-content:space-between;padding:0 89px 0 92px;font-size:14px;color:#ddd}
  .site-footer .company{color:var(--gold)}
  .footer-links{display:flex;gap:26px}
</style>
</head>
<body>
<div class="page">

  <header class="site-header">
    <div class="brand">
      <div class="brand-mark"></div>
      <div>
        <div class="brand-name">Evergreen Intimates</div>
        <div class="brand-tag">PRIVATE · DISCREET · CARING</div>
      </div>
    </div>
    <div class="account">
      <span>LOGIN / SIGNUP</span>
      <span class="cart">
        <svg width="16" height="14" viewBox="0 0 16 14"><path d="M1 1h3l2 8h8l1.5-6H5" fill="none" stroke="#ddd" stroke-width="1.5"/><circle cx="7" cy="12" r="1.3" fill="#ddd"/><circle cx="13" cy="12" r="1.3" fill="#ddd"/></svg>
        $ 100.00
      </span>
    </div>
    <nav class="main-nav">
      <a class="active" href="#">Homepage</a><span class="dot"></span>
      <a href="#">Products</a><span class="dot"></span>
      <a href="#">Services</a><span class="dot"></span>
      <a href="#">Shipping</a><span class="dot"></span>
      <a href="#">Payment</a><span class="dot"></span>
      <a href="#">Help</a><span class="dot"></span>
      <a href="#">Contact</a>
    </nav>
  </header>

  <div class="hero" role="img" aria-label="Hero photograph of an affectionate couple embracing in warm low light"></div>

  <div class="search-bar">
    <div class="search-label">Search Products</div>
    <div class="search-field" style="width:277px">
      <svg width="10" height="10" viewBox="0 0 10 10"><path d="M1 9l6-6 1 1-6 6z" fill="#777"/></svg>
    </div>
    <div class="search-field" style="width:175px;margin-left:6px">
      <svg width="10" height="10" viewBox="0 0 10 10"><rect x="1" y="4" width="8" height="5" fill="#777"/><rect x="3" y="1" width="4" height="3" fill="#777"/></svg>Categories
    </div>
    <div class="search-field" style="width:181px;margin-left:17px">
      <svg width="9" height="12" viewBox="0 0 9 12"><path d="M4.5 0a4.5 4.5 0 0 1 4.5 4.5C9 8 4.5 12 4.5 12S0 8 0 4.5A4.5 4.5 0 0 1 4.5 0z" fill="#777"/><circle cx="4.5" cy="4.5" r="1.6" fill="#fff"/></svg>Locations
    </div>
    <div class="search-btn">Search</div>
  </div>

  <section class="store">
    <h1 class="section-title">WELCOME TO OUR STORE</h1>
    <div class="rule"></div>
    <p class="store-intro">FLorem ipsum dolor sit amet voluptatem fugit aut illo omnis explicabo ipsa nemo rem ipsam quasi illo dolores ut voluptatem doloremque perspiciatis beatae magni architeco</p>

    <div class="product-grid">
      <article class="product-card">
        <div class="product-img" role="img" aria-label="Product photo: pink couples toy on a light background" style="background:radial-gradient(ellipse 30% 42% at 52% 52%,#d96bbd,#e9a8d6 55%,rgba(236,236,236,0) 100%),#ececec"></div>
        <h3>NEW ARRIVALS</h3><div class="rule"></div>
        <p>Lorem ipsum dolor sit amet voluptatem fugit illo omnisa explicabo nemo rem ipsam quas dolores voluptatem doloremque perspiciatis</p>
        <div class="card-actions"><span class="btn-more">LEARN MORE</span><span class="btn-cart"><svg width="18" height="15" viewBox="0 0 16 14"><path d="M1 1h3l2 8h8l1.5-6H5" fill="none" stroke="#fff" stroke-width="1.6"/><circle cx="7" cy="12" r="1.3" fill="#fff"/><circle cx="13" cy="12" r="1.3" fill="#fff"/></svg></span></div>
      </article>
      <article class="product-card">
        <div class="product-img" role="img" aria-label="Product photo: bright pink flexible massager" style="background:radial-gradient(ellipse 42% 36% at 55% 50%,#f05cc4,#f39ad8 55%,rgba(238,226,240,0) 100%),#eee2f0"></div>
        <h3>TOP PRODUCTS</h3><div class="rule"></div>
        <p>Lorem ipsum dolor sit amet voluptatem fugit illo omnisa explicabo nemo rem ipsam quas dolores voluptatem doloremque perspiciatis</p>
        <div class="card-actions"><span class="btn-more">LEARN MORE</span><span class="btn-cart"><svg width="18" height="15" viewBox="0 0 16 14"><path d="M1 1h3l2 8h8l1.5-6H5" fill="none" stroke="#fff" stroke-width="1.6"/><circle cx="7" cy="12" r="1.3" fill="#fff"/><circle cx="13" cy="12" r="1.3" fill="#fff"/></svg></span></div>
      </article>
      <article class="product-card">
        <div class="product-img" role="img" aria-label="Product photo: soft skin-tone novelty item" style="background:radial-gradient(ellipse 30% 36% at 52% 55%,#d99a5c,#e8b886 55%,rgba(236,236,236,0) 100%),#ececec"></div>
        <h3>PROMOS</h3><div class="rule"></div>
        <p>Lorem ipsum dolor sit amet voluptatem fugit illo omnisa explicabo nemo rem ipsam quas dolores voluptatem doloremque perspiciatis</p>
        <div class="card-actions"><span class="btn-more">LEARN MORE</span><span class="btn-cart"><svg width="18" height="15" viewBox="0 0 16 14"><path d="M1 1h3l2 8h8l1.5-6H5" fill="none" stroke="#fff" stroke-width="1.6"/><circle cx="7" cy="12" r="1.3" fill="#fff"/><circle cx="13" cy="12" r="1.3" fill="#fff"/></svg></span></div>
      </article>
      <article class="product-card">
        <div class="product-img" role="img" aria-label="Product photo: textured personal accessory" style="background:radial-gradient(ellipse 32% 45% at 45% 50%,#e6c1aa,#ecd6c8 55%,rgba(220,214,228,0) 100%),#dcd6e4"></div>
        <h3>FOR INDIVIDUALS</h3><div class="rule"></div>
        <p>Lorem ipsum dolor sit amet voluptatem fugit illo omnisa explicabo nemo rem ipsam quas dolores voluptatem doloremque perspiciatis</p>
        <div class="card-actions"><span class="btn-more">LEARN MORE</span><span class="btn-cart"><svg width="18" height="15" viewBox="0 0 16 14"><path d="M1 1h3l2 8h8l1.5-6H5" fill="none" stroke="#fff" stroke-width="1.6"/><circle cx="7" cy="12" r="1.3" fill="#fff"/><circle cx="13" cy="12" r="1.3" fill="#fff"/></svg></span></div>
      </article>
      <article class="product-card">
        <div class="product-img" role="img" aria-label="Product photo: pink plush cuffs for couples" style="background:radial-gradient(ellipse 42% 32% at 50% 42%,#ef8fbc,#f4b6d2 55%,rgba(230,234,244,0) 100%),#e6eaf4"></div>
        <h3>FOR COUPLES</h3><div class="rule"></div>
        <p>Lorem ipsum dolor sit amet voluptatem fugit illo omnisa explicabo nemo rem ipsam quas dolores voluptatem doloremque perspiciatis</p>
        <div class="card-actions"><span class="btn-more">LEARN MORE</span><span class="btn-cart"><svg width="18" height="15" viewBox="0 0 16 14"><path d="M1 1h3l2 8h8l1.5-6H5" fill="none" stroke="#fff" stroke-width="1.6"/><circle cx="7" cy="12" r="1.3" fill="#fff"/><circle cx="13" cy="12" r="1.3" fill="#fff"/></svg></span></div>
      </article>
      <article class="product-card">
        <div class="product-img" role="img" aria-label="Product photo: purple curved device" style="background:radial-gradient(ellipse 34% 30% at 52% 52%,#7a3a86,#a774b0 55%,rgba(244,244,244,0) 100%),#f4f4f4"></div>
        <h3>OTHER PRODUCTS</h3><div class="rule"></div>
        <p>Lorem ipsum dolor sit amet voluptatem fugit illo omnisa explicabo nemo rem ipsam quas dolores voluptatem doloremque perspiciatis</p>
        <div class="card-actions"><span class="btn-more">LEARN MORE</span><span class="btn-cart"><svg width="18" height="15" viewBox="0 0 16 14"><path d="M1 1h3l2 8h8l1.5-6H5" fill="none" stroke="#fff" stroke-width="1.6"/><circle cx="7" cy="12" r="1.3" fill="#fff"/><circle cx="13" cy="12" r="1.3" fill="#fff"/></svg></span></div>
      </article>
    </div>
    <div class="see-more">SEE MORE PRODUCTS</div>
  </section>

  <section class="news">
    <div class="news-col">
      <h2>RECENT NEWS</h2>
      <h3>Omnis aut aperiam ab ipsam ipsa odit aut aperiam aut aspernatur veritatis unde</h3>
      <div class="news-date">April 28, 2015</div>
      <p>Lorem ipsum dolor sit amet voluptatem fugit aut illo omnisap explicabo nemo rem ipsam quasi illo dolores voluptatem doloremque perspiciatis magni architecto odit odit, aspernatur magni quae aperiam aut veritatis eos aut voluptas doloremque perspiciati error natus illo natus inventore aut quasi consequuntur consequuntur ipsa odit aspernatur iste ut quae explicabo dicta quasi...</p>
      <div class="read-more">Read more</div>
    </div>
    <div class="news-col">
      <h2>RELATIONSHIP ISSUES</h2>
      <h3>Ipsam ipsa odit aut aperiam aut aspernatur veritatis unde omnis aut aperiam ab</h3>
      <div class="news-date">April 28, 2015</div>
      <p>Lorem ipsum dolor sit amet voluptatem fugit aut illo omnisap explicabo nemo rem ipsam quasi illo dolores voluptatem doloremque perspiciatis magni architecto odit odit, aspernatur magni quae aperiam aut veritatis eos aut voluptas doloremque perspiciati error natus illo natus inventore aut quasi consequuntur consequuntur ipsa odit aspernatur iste ut quae explicabo dicta quasi...</p>
      <div class="read-more">Read more</div>
    </div>
  </section>

  <section class="subscribe">
    <div class="subscribe-bg" role="img" aria-label="Soft-focus background photograph of a couple in dim evening light"></div>
    <div class="subscribe-inner">
      <div class="social"><span></span><span></span><span></span><span></span></div>
      <h2>PLEASE SUBSCRIBE</h2>
      <p>Get our newsletter for various sex new release, promo of the month and relationship issues</p>
      <div class="subscribe-form"><div class="field"></div><div class="go">Subscribe</div></div>
      <div class="stats">
        <div class="stat"><strong>180 MILLION</strong><span>Products</span></div>
        <div class="stat"><strong>860 MILLION</strong><span>Members</span></div>
        <div class="stat"><strong>250 MILLION</strong><span>Problem Solved</span></div>
        <div class="stat"><strong>109 MILLION</strong><span>Followers</span></div>
      </div>
    </div>
  </section>

  <footer class="site-footer">
    <div>© 2015 <span class="company">EVERGREEN INTIMATES</span></div>
    <div class="footer-links"><span>About us</span><span>Privacy policy</span><span>Terms and use</span><span>Countries</span><span>FAQ</span><span>Contact</span></div>
  </footer>

</div>
</body>
</html>
```